Beauty Therapy Web Design

I need a web page design for a small beauty therapy clinic, the owner is currently the only beauty therapist working there.
We require the following pages:
Home
About
Treatments
Nails
Courses
Contact
I will attach the clinics business card, treatment menu and signage so that you get a feeling for the branding colours etc.
This is the first website for the beauty therapist, she would like to attract new clients and also tourists that come in on the cruise ships. The thing that sets her apart from other clinics is that she welcomes texting for appointments.
I have selected refundable because I have never done this before so I don't know what to expect, I have the full intention of going through with it as long as I get a good design.
Feel free to ask for further information
Reason: Project extended as I am away for work and am unable to meet with the owner.
Target Market(s)
Females 18 to 50
Industry/Entity Type
Business
Look and feel

```html
<!DOCTYPE html>
<html lang="en">
<head>
<meta charset="utf-8">
<title>Lumina Beauty Therapy</title>
<link rel="stylesheet" href="https://fonts.googleapis.com/css2?family=Arimo:wght@400;700&display=swap">
<style>
  :root {
    --ink: #2e2159;
    --ink-soft: #3b2a5e;
    --brand: #4b2aa8;
    --nav-bg: #000000;
    --nav-line: #8a8a8a;
    --white: #ffffff;
    --glow: rgba(120, 90, 230, 0.28);
    --btn-top: #957af0;
    --btn-bottom: #5b38cc;
    --btn-edge: #6a47d6;
    --dot: #7250dc;
    --dot-active: #d9ccf8;
    --footer-top: #ffffff;
    --footer-bottom: #efebf8;
  }
  * { box-sizing: border-box; margin: 0; padding: 0; }
  html, body { width: 1200px; height: 1139px; overflow: hidden; }
  body {
    position: relative;
    background: var(--white);
    font-family: "Arimo", Arial, sans-serif;
    color: var(--ink);
  }
  .brand {
    position: absolute; left: 121px; top: 34px;
    color: var(--brand); font-weight: 700; line-height: 1;
  }
  .brand-name { font-size: 92px; letter-spacing: -1px; display: block; }
  .brand-tag { font-size: 38px; display: block; margin-top: 10px; letter-spacing: 1px; text-transform: uppercase; }
  .header-contact {
    position: absolute; right: 129px; top: 60px; text-align: right;
    color: var(--ink-soft); font-size: 15px; line-height: 28px;
  }
  .header-contact strong { font-weight: 400; font-size: 19px; margin-left: 4px; }
  .header-address {
    position: absolute; right: 129px; top: 158px;
    color: var(--ink-soft); font-size: 15px;
  }
  .main-nav {
    position: absolute; left: 47px; top: 198px; width: 1102px; height: 34px;
    background: var(--nav-bg); border-radius: 17px;
  }
  .main-nav a {
    position: absolute; top: 0; line-height: 34px; transform: translateX(-50%);
    color: var(--white); font-weight: 700; font-size: 14px; text-decoration: none;
  }
  .nav-divider { position: absolute; top: 9px; width: 1px; height: 18px; background: var(--nav-line); }
  .hero {
    position: absolute; left: 47px; top: 257px; width: 1102px; height: 350px;
    background: var(--white); box-shadow: 0 0 30px 8px var(--glow);
  }
  .hero-photo {
    position: absolute; left: 0; top: 0; width: 469px; height: 350px;
    background: radial-gradient(ellipse at 45% 50%, #f0cdbd 0%, #e9b7a6 30%, #b79ae6 55%, #ffffff 80%);
  }
  .hero-copy { position: absolute; left: 565px; top: 38px; width: 480px; }
  .hero-title { font-size: 36px; font-weight: 700; color: var(--ink); letter-spacing: 0.3px; }
  .hero-lead { font-size: 17px; font-weight: 700; margin-top: 12px; }
  .hero-text { font-size: 16px; line-height: 30px; margin-top: 20px; letter-spacing: 0.3px; }
  .read-more {
    position: absolute; display: block; width: 233px; height: 46px;
    border-radius: 23px; border: 2px solid var(--btn-edge);
    background: linear-gradient(var(--btn-top), var(--btn-bottom));
    color: var(--white); font-weight: 700; font-size: 23px; line-height: 42px;
    text-align: center; text-decoration: none;
    text-shadow: 0 1px 3px rgba(0, 0, 0, 0.6);
  }
  .hero .read-more { left: 658px; top: 213px; }
  .slider-dots { position: absolute; left: 703px; top: 304px; display: flex; gap: 7px; }
  .slider-dots span {
    width: 23px; height: 23px; border-radius: 50%;
    background: radial-gradient(circle at 40% 35%, #9f85f0, var(--dot));
  }
  .slider-dots .is-active { background: radial-gradient(circle at 40% 35%, #ffffff, var(--dot-active)); }
  .treatment-card {
    position: absolute; top: 643px; width: 328px; height: 357px;
    background: var(--white); box-shadow: 0 0 24px 4px rgba(120, 90, 230, 0.12);
    padding: 22px 0 0 48px;
  }
  .treatment-card h2 { font-size: 23px; font-weight: 700; }
  .treatment-card .card-lead { font-size: 16px; font-weight: 700; line-height: 29px; margin-top: 26px; width: 250px; }
  .treatment-card .card-text { font-size: 16px; line-height: 29.5px; margin-top: 26px; width: 260px; letter-spacing: 0.2px; }
  .treatment-card .read-more { left: 48px; top: 287px; }
  .site-footer {
    position: absolute; left: 47px; top: 1002px; width: 1102px; height: 137px;
    background: linear-gradient(var(--footer-top), var(--footer-bottom));
    text-align: center; color: var(--ink-soft); font-size: 15px; line-height: 28px;
    padding-top: 34px;
  }
  .site-footer span + span { margin-left: 18px; }
</style>
</head>
<body>
  <header>
    <div class="brand">
      <span class="brand-name">Lumina</span>
      <span class="brand-tag">Beauty Therapy</span>
    </div>
    <div class="header-contact">
      <div>Phone Talia <strong>07 555 0142</strong></div>
      <div>Cellphone <strong>027 555 0198</strong></div>
    </div>
    <div class="header-address">Cnr Kauri St. &amp; Harbour Rd, Bayview</div>
    <nav class="main-nav">
      <span class="nav-divider" style="left:153px"></span>
      <a href="#" style="left:208px">HOME</a>
      <span class="nav-divider" style="left:264px"></span>
      <a href="#" style="left:324px">ABOUT</a>
      <span class="nav-divider" style="left:384px"></span>
      <a href="#" style="left:466px">TREATMENTS</a>
      <span class="nav-divider" style="left:550px"></span>
      <a href="#" style="left:605px">NAILS</a>
      <span class="nav-divider" style="left:661px"></span>
      <a href="#" style="left:741px">COURSES</a>
      <span class="nav-divider" style="left:811px"></span>
      <a href="#" style="left:879px">CONTACT</a>
      <span class="nav-divider" style="left:948px"></span>
    </nav>
  </header>

  <section class="hero">
    <div class="hero-photo" role="img" aria-label="Photo of a hand with purple painted nails holding a nail polish bottle"></div>
    <div class="hero-copy">
      <h1 class="hero-title">SPA DELUXE MANICURE</h1>
      <p class="hero-lead">Homero nostrum definitionem mea et, his no malis</p>
      <p class="hero-text">Homero nostrum definitionem mea et, his no malis ullamcorper, cu tollit nostrum pri. Qui id nusquam docendi</p>
    </div>
    <a class="read-more" href="#">Read more</a>
    <div class="slider-dots">
      <span></span><span class="is-active"></span><span></span><span></span><span></span>
    </div>
  </section>

  <article class="treatment-card" style="left:47px">
    <h2>G Wax</h2>
    <p class="card-lead">Homero nostrum definitionem mea et, his no malis</p>
    <p class="card-text">Homero nostrum definitionem mea et, his no malis ullamcorper, cu tollit nostrum pri. Qui id</p>
    <a class="read-more" href="#">Read more</a>
  </article>
  <article class="treatment-card" style="left:434px">
    <h2>Bikini</h2>
    <p class="card-lead">Homero nostrum definitionem mea et, his no malis</p>
    <p class="card-text">Homero nostrum definitionem mea et, his no malis ullamcorper, cu tollit nostrum pri. Qui id</p>
    <a class="read-more" href="#">Read more</a>
  </article>
  <article class="treatment-card" style="left:821px">
    <h2>Brazilian Waxing</h2>
    <p class="card-lead">Homero nostrum definitionem mea et, his no malis</p>
    <p class="card-text">Homero nostrum definitionem mea et, his no malis ullamcorper, cu tollit nostrum pri. Qui id</p>
    <a class="read-more" href="#">Read more</a>
  </article>

  <footer class="site-footer">
    <div>Copyright 2012 Lumina Beauty Therapy</div>
    <div><span>Phone Talia 07 555 0142</span><span>Cellphone 027 555 0198</span></div>
    <div>Cnr Kauri St. &amp; Harbour Rd, Bayview</div>
  </footer>
</body>
</html>
```